Web Design Project

We have a website in beta that needs updating and are looking for a freash new look for the Home page including Logo.
Our company is called " Kip Dorra " we specialize in classified advertising using video. Our consumers will be businesses selling a product or service. Please visit www.kipdorra.com
Our aim past this point is to engage a developer to write the code based on the best design. Our target market is the U.S and I have included some of the landing pages to give you a better idea of what we are trying to acheive

http://www.kipdorra.com/
http://www.kipdorra.com/cars_home.php
http://www.kipdorra.com/boats.php
http://www.kipdorra.com/electronic.php
http://www.kipdorra.com/realestate.php
http://www.kipdorra.com/roommates.php
Updates

Target Market(s)

20-35 yr old people who are connected to the internet via mobile phone and use social media on a daily/weekly basis

Industry/Entity Type

Advertising

Requirements
Must have
• We would like to use lots of images to convey it is a video driven website business
Nice to have
• Logo to incorporate same theme of website ( ie ) you are here to watch videos of thinhs to buy & sell
Should not have
• This is to be a freash new site with large type and bold fonts

```html
<!DOCTYPE html>
<html lang="en">
<head>
<meta charset="utf-8">
<title>Kip Dorra — Home</title>
<link href="https://fonts.googleapis.com/css2?family=PT+Sans:wght@400;700&family=Arimo:wght@400;700&display=swap" rel="stylesheet">
<style>
:root{
  --blue:#2fa8dc;
  --blue-light:#5cc4ee;
  --blue-dark:#1a8cc4;
  --text:#3a3a3a;
  --muted:#666;
  --line:#d8d8d8;
  --panel-bg:#ededed;
  --white:#fff;
  --btn-dark:#555;
}
*{margin:0;padding:0;box-sizing:border-box}
html,body{width:945px;height:1200px;overflow:hidden;background:var(--white)}
body{position:relative;font-family:"PT Sans",sans-serif;color:var(--text)}
.abs{position:absolute}

/* header */
.brand{left:146px;top:30px;font:700 30px "PT Sans",sans-serif;color:var(--blue);display:flex;align-items:center;gap:8px}
.brand .dot{width:14px;height:14px;background:var(--blue);border-radius:50%}
.top-links{left:527px;top:50px;font:700 9px "Arimo",sans-serif;color:#555;display:flex;gap:9px}
.search{left:626px;top:47px;width:157px;height:18px;border:1px solid #ddd;border-radius:2px;font:9px "Arimo",sans-serif;color:#888;padding:4px 6px}
.search svg{position:absolute;right:6px;top:2px}

/* nav */
.nav{left:0;top:82px;width:945px;height:29px;border-top:1px solid var(--line);border-bottom:1px solid var(--line);background:linear-gradient(#fff,#f4f4f4)}
.nav ul{position:absolute;left:139px;top:-1px;display:flex;list-style:none;height:29px}
.nav li{font:700 8.5px "Arimo",sans-serif;color:#444;padding:0 9px;line-height:29px;border-right:1px solid var(--line);letter-spacing:.2px}
.nav li:first-child{border-left:1px solid var(--line)}
.nav li.active{background:var(--blue);color:#fff;padding:0 10px}

/* featured */
.featured{left:148px;top:132px;width:647px;height:471px;border:1px solid #cfcfcf;border-radius:3px;box-shadow:0 1px 3px rgba(0,0,0,.1)}
.band-title{background:linear-gradient(var(--blue-light),var(--blue));color:#fff;font-size:13.5px;height:27px;line-height:27px;padding-left:17px}
.card{position:absolute;width:166px}
.card .photo{width:166px;height:123px;border:4px solid #b5b5b5;box-shadow:0 2px 3px rgba(0,0,0,.25)}
.card p{font-size:8.5px;line-height:15px;color:#444;margin:8px 0 0 18px;width:140px}
.go{position:absolute;right:7px;top:162px;width:61px;height:23px;border:1px solid #ccc;border-radius:2px;background:linear-gradient(#fff,#eee);font-size:10.5px;color:#333;line-height:21px;padding-left:18px}
.go::before{content:"";position:absolute;left:6px;top:7px;border-left:4px solid #4a8fcf;border-top:4px solid transparent;border-bottom:4px solid transparent}
.go::after{content:"";position:absolute;left:14px;top:4px;height:13px;border-left:1px solid #ccc}

/* lower band */
.lower-bg{left:0;top:679px;width:945px;height:285px;background:var(--panel-bg);border-top:2px solid var(--blue);border-bottom:2px solid var(--blue)}
.lower-head{left:148px;top:659px;width:648px;height:42px;background:linear-gradient(var(--blue-light),var(--blue));box-shadow:0 2px 3px rgba(0,0,0,.2);color:#fff;font-size:13.5px}
.lower-head span{position:absolute;top:13px}
.step{top:724px;width:72px;height:95px}
.step .art{width:66px;height:66px;margin-left:3px;border-radius:50%;background:radial-gradient(#e8e8e8,#b7b7b7)}
.step .arrow{margin-top:2px;height:26px;position:relative}
.step .arrow span{position:absolute;left:6px;top:4px;color:#fff;font-size:11px}
.how-text{left:152px;top:842px;width:335px;font-size:8.5px;line-height:15px;color:#444}
.read-more{left:168px;top:916px;width:102px;height:22px;background:linear-gradient(#777,#4a4a4a);border-radius:2px;color:#fff;font-size:10.5px;line-height:22px;padding-left:17px;box-shadow:0 0 0 2px #fff}
.read-more i{position:absolute;right:7px;top:6px;width:10px;height:10px;border-radius:50%;background:#222;border:1px solid #999}
.blog{left:527px;width:258px}
.blog .thumb{position:absolute;left:0;top:0;width:53px;height:51px;border:3px solid #fff;box-shadow:0 1px 2px rgba(0,0,0,.3)}
.blog h4{position:absolute;left:61px;top:0;font-weight:400;font-size:10.5px;color:#555}
.blog p{position:absolute;left:61px;top:16px;width:190px;font-size:8.5px;line-height:10px;color:#333}
.dots{left:527px;width:256px;border-top:1px dotted #aaa}

/* footer */
.fcol{top:995px}
.fcol h3{font-weight:400;font-size:13.5px;color:#333;padding-bottom:5px;border-bottom:1px solid #ddd;letter-spacing:.3px}
.fcol ul{list-style:none;margin-top:14px}
.fcol li{font-size:8.5px;color:#444;height:19px;padding-left:14px;position:relative}
.fcol li::before{content:"+";position:absolute;left:2px;top:-1px;font-size:7px}
.social{display:flex;align-items:center;gap:12px;height:38px;font-size:8.5px;color:#333}
.social .sq{width:30px;height:30px;border-radius:6px;border:2px solid #ccc}
.bottom-bar{left:0;top:1176px;width:945px;height:24px;background:var(--blue);color:#e6f6fd;font:7.5px "Arimo",sans-serif;padding:8px 0 0 150px}
</style>
</head>
<body>

<header>
  <div class="abs brand"><span>Kip Dorra</span><span class="dot"></span></div>
  <div class="abs top-links"><span>Creat an Ad</span><span>Sing-in</span></div>
  <div class="abs search">Search
    <svg width="12" height="12" viewBox="0 0 12 12"><circle cx="7" cy="5" r="3.5" fill="none" stroke="#335" stroke-width="1.4"/><line x1="4.5" y1="7.5" x2="1" y2="11" stroke="#335" stroke-width="1.8"/></svg>
  </div>
</header>

<nav class="abs nav">
  <ul>
    <li class="active">HOME</li><li>CARS</li><li>BOATS</li><li>ELECTRONICS</li><li>REAL ESTATE</li><li>ROOMMATES</li><li>OTHER CATEGORIES</li><li>MY ACCOUNT</li>
  </ul>
</nav>

<section class="abs featured">
  <div class="band-title">Browse: Featured On Kip Dorra.</div>

  <div class="card" style="left:25px;top:45px">
    <div class="photo" role="img" aria-label="Red sports car" style="background:linear-gradient(135deg,#111,#7a1010 55%,#222)"></div>
    <p>Lorem Ipsum passages, recently publishing like Quill PageComposer including.</p>
    <span class="go">Go Now</span>
  </div>
  <div class="card" style="left:234px;top:45px">
    <div class="photo" role="img" aria-label="White motor yacht on the water" style="background:linear-gradient(#6ea4d8,#e9eef3 55%,#2c4f74)"></div>
    <p>Lorem Ipsum passages, recently publishing like Quill PageComposer including.</p>
    <span class="go">Go Now</span>
  </div>
  <div class="card" style="left:442px;top:45px">
    <div class="photo" role="img" aria-label="Two-storey house" style="background:linear-gradient(#a9c3d9,#8e9a7b 35%,#8c5a4a 75%,#6d7a4c)"></div>
    <p>Lorem Ipsum passages, recently publishing like Quill PageComposer including.</p>
    <span class="go">Go Now</span>
  </div>
  <div class="card" style="left:25px;top:259px">
    <div class="photo" role="img" aria-label="Television and home audio set" style="background:linear-gradient(135deg,#f2f2f2,#3a3a3a 45%,#111)"></div>
    <p>Lorem Ipsum passages, recently publishing like Quill PageComposer including.</p>
    <span class="go">Go Now</span>
  </div>
  <div class="card" style="left:234px;top:259px">
    <div class="photo" role="img" aria-label="Shared room with a sofa" style="background:linear-gradient(135deg,#5a4a3a,#6d8a3c 55%,#3a3a3a)"></div>
    <p>Lorem Ipsum passages, recently publishing like Quill PageComposer including.</p>
    <span class="go">Go Now</span>
  </div>
  <div class="card" style="left:442px;top:259px">
    <div class="photo" role="img" aria-label="Private jet on the runway" style="background:linear-gradient(#9aa2ab,#c8ccd0 50%,#c87a3a 80%,#5a3a2a)"></div>
    <p>Lorem Ipsum passages, recently publishing like Quill PageComposer including.</p>
    <span class="go">Go Now</span>
  </div>
</section>

<div class="abs lower-bg"></div>
<div class="abs lower-head"><span style="left:11px">How It Works!</span><span style="left:389px;top:15px">From The Blog</span></div>

<section>
  <div class="abs step" style="left:168px">
    <div class="art" role="img" aria-label="Phone and video camera"></div>
    <div class="arrow"><svg width="72" height="26"><path d="M2 5h50V0l18 13-18 13v-5H2z" fill="#3b8fd6"/></svg><span>Create it</span></div>
  </div>
  <div class="abs step" style="left:287px">
    <div class="art" role="img" aria-label="Upload illustration"></div>
    <div class="arrow"><svg width="72" height="26"><path d="M2 5h50V0l18 13-18 13v-5H2z" fill="#5cb52e"/></svg><span>Upload it</span></div>
  </div>
  <div class="abs step" style="left:406px">
    <div class="art" role="img" aria-label="Seller holding a product"></div>
    <div class="arrow"><svg width="72" height="26"><path d="M2 5h50V0l18 13-18 13v-5H2z" fill="#e0432b"/></svg><span style="left:22px">Sell it</span></div>
  </div>
  <p class="abs how-text">Nulla tempor lectus a justo vulputate ut rutrum odio porttitor. Pellentesque a consectetur lectus. Suspendisse potenti. Duis consectetur vehicula justo, imperdiet viverra leo blandit ut. Duis venenatis lorem et nibh interdum rhoncus. Sed a erat id</p>
  <div class="abs read-more">Read More<i></i></div>
</section>

<section>
  <article class="abs blog" style="top:722px">
    <div class="thumb" role="img" aria-label="Television set" style="background:linear-gradient(#ddd,#222)"></div>
    <h4>Most Viewed</h4>
    <p>One in about every 10 adults you see walking around doesn't have a job right now.</p>
  </article>
  <div class="abs dots" style="top:784px"></div>
  <article class="abs blog" style="top:804px">
    <div class="thumb" role="img" aria-label="Home cinema scene" style="background:linear-gradient(#2a3a7a,#b02a2a)"></div>
    <h4>Most Recent</h4>
    <p>150-in 1080p high definition immersive TV for under $1,000?&nbsp; Yeah right.&nbsp; What about a......</p>
  </article>
  <div class="abs dots" style="top:865px"></div>
  <article class="abs blog" style="top:886px">
    <div class="thumb" role="img" aria-label="Father and son" style="background:linear-gradient(#cfd8dc,#b07a5a)"></div>
    <h4>Most Intersting</h4>
    <p>It seems like every year it gets harder and harder to find the perfect gift for dad.</p>
  </article>
</section>

<footer>
  <div class="abs fcol" style="left:144px;width:112px">
    <h3>BUY / BROWSE</h3>
    <ul><li>Roommates</li><li>Cars</li><li>Boats</li><li>Electronics</li><li>Others</li></ul>
  </div>
  <div class="abs fcol" style="left:272px;width:105px">
    <h3>SELL</h3>
    <ul><li>Start Selling</li><li>Login</li><li>Shooting Video</li><li>Uploading Video</li><li>Buying</li></ul>
  </div>
  <div class="abs fcol" style="left:402px;width:108px">
    <h3>INFO</h3>
    <ul><li>VBlog</li><li>FAQs</li><li>Terms of Use</li><li>Privacy Policy</li><li>Buyer/Seller Safety</li></ul>
  </div>
  <div class="abs fcol" style="left:529px;width:105px">
    <h3>CONTACT</h3>
    <ul><li>Contact Us</li><li>Feedback Form</li><li>Referral Program</li><li>Business Register</li><li>Subscription</li></ul>
  </div>
  <div class="abs fcol" style="left:653px;width:123px">
    <h3>CONNECT</h3>
    <div style="margin-top:10px">
      <div class="social"><span class="sq" style="background:#3b5998"></span>Join Us on Friendspace</div>
      <div class="social"><span class="sq" style="background:#33b5e5"></span>Follow us on Chirpline</div>
      <div class="social"><span class="sq" style="background:#e8601c"></span>RSS Feed</div>
    </div>
  </div>
  <div class="abs bottom-bar">© 2011 Kip Dorra All Rights Reserved</div>
</footer>

</body>
</html>
```